Forensic Document Examiner, looking for contemporary update to my stationery design.

Looking for professional, classy logo design for stationery and business cards. My current stationery and business card is attached.I believe a logo image makes a header section interesting, so an intriguing design of a pen, feathered pen, microscope, magnifying glass, etc., would be appropriate. I have been in the business for over 30 years. I leave ideas to the imagination of the designer.My work involves mainly, the comparison of signatures and handwriting. I also resolve alterations, obliterations, and work as shown on my website: www.documentexaminer.infoThe image produced will be printed on quality white stationery and envelopes. The stationery will be photocopied by my clients, so the images should be reproducible. The business cards may be designed in other than white.

Target Market(s)

Attorneys

Font styles to use
Sans Serif

Colors

Designer to choose colors to be used in the design.

Requirements
Must have
• Image suitable for white stationery and photocopying.
• Classy logo and image; no casual fonts.
Nice to have
• Intriguing, contemporary design incorporating a relevant logo to my work.

```html
<!DOCTYPE html>
<html lang="en">
<head>
<meta charset="utf-8">
<title>Daniel R. Hale – Business Card</title>
<link rel="stylesheet" href="https://fonts.googleapis.com/css2?family=Arvo&family=PT+Sans:ital,wght@0,400;0,700;1,400&display=swap">
<style>
  :root {
    --backdrop: #7a5a40;
    --card: #2d2d2d;
    --card-edge: #232323;
    --accent: #f2d22a;
    --text-light: #ececec;
    --text-muted: #c4c4c4;
  }
  * { margin: 0; padding: 0; box-sizing: border-box; }
  html, body {
    width: 1125px;
    height: 1200px;
    overflow: hidden;
    background: var(--backdrop);
  }
  .canvas {
    position: relative;
    width: 1125px;
    height: 1200px;
  }
  .card {
    position: absolute;
    left: 150px;
    width: 825px;
    height: 470px;
    border-radius: 24px;
    background: linear-gradient(90deg, var(--card) 0%, var(--card) 70%, var(--card-edge) 100%);
    box-shadow: 0 6px 10px rgba(0,0,0,0.45);
    font-family: "PT Sans", sans-serif;
  }
  .card--front { top: 100px; }
  .card--back { top: 632px; }

  /* front */
  .brand-mark {
    position: absolute;
    right: 60px;
    top: 88px;
    display: flex;
    align-items: center;
    gap: 10px;
    color: var(--text-muted);
    font-size: 18px;
    font-weight: 700;
    letter-spacing: 0.5px;
  }
  .brand-mark .dot {
    width: 14px; height: 14px;
    border-radius: 50%;
    background: var(--text-muted);
  }
  .holder {
    position: absolute;
    left: 48px;
    top: 250px;
  }
  .holder__name {
    font-family: "Arvo", serif;
    color: var(--accent);
    font-size: 29px;
    line-height: 1.1;
  }
  .holder__title {
    color: var(--text-light);
    font-size: 20px;
    margin-top: 2px;
  }
  .contacts {
    list-style: none;
    margin-top: 16px;
  }
  .contacts li {
    display: flex;
    align-items: center;
    gap: 12px;
    color: var(--text-light);
    font-size: 18px;
    line-height: 25px;
  }
  .contacts svg { width: 16px; height: 16px; fill: var(--accent); flex: none; }

  /* back */
  .lockup {
    position: absolute;
    left: 0; right: 0;
    top: 138px;
    text-align: center;
  }
  .lockup__name {
    display: inline-flex;
    align-items: center;
    gap: 16px;
    color: #f4f4f4;
    font-size: 60px;
    font-weight: 400;
    letter-spacing: 5px;
    line-height: 1;
  }
  .lockup__name .dot {
    width: 22px; height: 22px;
    border-radius: 50%;
    background: #c9c9c9;
  }
  .lockup__role {
    margin-top: 14px;
    color: var(--accent);
    font-size: 26px;
    font-weight: 700;
  }
  .services {
    position: absolute;
    left: 0; right: 0;
    top: 370px;
    text-align: center;
    color: var(--text-muted);
    font-style: italic;
    font-size: 18px;
    line-height: 25px;
  }
</style>
</head>
<body>
<main class="canvas">
  <section class="card card--front">
    <div class="brand-mark"><span class="dot"></span>Daniel R. Hale</div>
    <div class="holder">
      <h1 class="holder__name">Daniel R. Hale</h1>
      <p class="holder__title">Forensic document Examiner</p>
      <ul class="contacts">
        <li><svg viewBox="0 0 16 16"><path d="M3.5 1.5l2.5 3-1.5 1.8c.9 2 2.4 3.5 4.4 4.4L10.7 9.2l3 2.5-1.3 2.3C7 14 2 9 2 3.5z"/></svg>(555) 214-0390</li>
        <li><svg viewBox="0 0 16 16"><path d="M1 3.5h14v9H1z M1.5 4l6.5 5 6.5-5" fill="none" stroke="#f2d22a" stroke-width="0"/><path d="M1 3.5h14L8 8.5z"/><path d="M1 5l7 5 7-5v7.5H1z"/></svg>dhale@quillmarkreview.info</li>
        <li><svg viewBox="0 0 16 16"><circle cx="8" cy="8" r="7"/><path d="M5 4c1.5 1 1 2.5 2.5 3s.5 2-.5 2.5-.5 2.5 1 3.5M11 3.5c-1 1.2-.5 2.3.8 2.5" fill="none" stroke="#2d2d2d" stroke-width="1.5"/></svg>www.quillmarkreview.info</li>
        <li><svg viewBox="0 0 16 16"><path d="M8 1a5 5 0 0 1 5 5c0 3.5-5 9-5 9S3 9.5 3 6a5 5 0 0 1 5-5zm0 3a2 2 0 1 0 0 4 2 2 0 0 0 0-4z"/></svg>P.O.Box 4821, Marlow, OR 97480</li>
      </ul>
    </div>
  </section>

  <section class="card card--back">
    <div class="lockup">
      <div class="lockup__name"><span class="dot"></span>DANIEL R. HALE</div>
      <p class="lockup__role">Forensic Document Examiner</p>
    </div>
    <p class="services">Full service laboratory, Specializing in handwriting comparisons,<br>obliterations, alterations indented wrinting recovery, etc.</p>
  </section>
</main>
</body>
</html>
```